I want a website to be designed for our new company, it's an import and export company for variety of things.

please see the attached Logo for our company and the Images for our different sections for our busienss

Target Market(s)

multiple

Coding

Coded - Design and coding required

Number of Pages Required

5+ page

Font styles to use
Sans Serif

Colors

Designer to choose colors to be used in the design.

Requirements
Must have
• KVR GLOBALINKS
• KVR globalinks Trading & Contracting provides various services. The Company offers infrastructure construction, oil, enegy and gas services, agricultural projects, real estate development, travel and tourism, and food processing and trading.
• Civil contracting for infrastructure, residential and heavy projects. Through its main subsidiaries; distribution of general food products, construction chemicals including corrosion inhibitors and electrical machinery; provides catering and travel agency services; ownership and operation of a school; offers human sources services including manpower supply.
• Drilling and Gold Mines Used Machinery, All Kinds of Construction Machinery, Drilling Machines are manufactured and sold.
Nice to have
• good designa and beautiful colours, it has too look professional

```html
<!DOCTYPE html>
<html lang="en">
<head>
<meta charset="utf-8">
<title>KVR GLOBALINKS – Trading &amp; Contracting</title>
<link href="https://fonts.googleapis.com/css2?family=Lato:wght@400;700;900&family=Poppins:wght@400;500&display=swap" rel="stylesheet">
<style>
:root{
  --gold:#c49a4f;
  --gold-dark:#a88141;
  --bg:#151515;
  --bar:#1d1d1d;
  --panel:#1f1f1f;
  --panel-2:#1a1a1a;
  --text:#ffffff;
  --muted:#cfcfcf;
}
*{margin:0;padding:0;box-sizing:border-box}
html,body{width:1200px;height:4392px;overflow:hidden}
body{position:relative;background:var(--bg);color:var(--text);font-family:"Lato",sans-serif}
.abs{position:absolute}
.center{transform:translateX(-50%);text-align:center;white-space:nowrap}

.topbar{left:0;top:0;width:1200px;height:34px;background:linear-gradient(90deg,var(--gold-dark),var(--gold),var(--gold-dark));font-size:12px;display:flex;align-items:center}
.topbar .info{position:absolute;display:flex;align-items:center;gap:8px}
.topbar .phone{font-size:22px;font-weight:700}
.navbar{left:0;top:34px;width:1200px;height:78px;background:var(--bar)}
.nav-link{top:67px;font-size:14px;font-weight:700;letter-spacing:.2px}
.nav-link.active{color:var(--gold)}
.nav-link.active::after{content:"";position:absolute;left:15%;right:15%;bottom:-8px;height:2px;background:var(--gold)}
.brand{left:116px;top:24px;width:154px;height:154px;border-radius:50%;background:#1b1b1b;display:flex;align-items:center;justify-content:center;font-size:15px;font-weight:700;letter-spacing:1px;color:var(--text);text-align:center;line-height:1.3;z-index:3}

.hero{left:0;top:112px;width:1200px;height:625px;background:linear-gradient(160deg,#2b3445 0%,#6a5a4a 35%,#b77a3c 55%,#2f4a73 80%,#1a2233 100%)}
.hero-title{left:522px;top:285px;font-family:"Poppins",sans-serif;font-size:54px;font-weight:500;letter-spacing:1px;text-shadow:0 2px 6px rgba(0,0,0,.4)}
.hero-sub{left:525px;top:374px;font-size:14px}
.btn{display:flex;align-items:center;justify-content:center;gap:10px;background:var(--gold);color:#fff;font-size:15px;font-weight:700;clip-path:polygon(10% 0,100% 0,90% 100%,0 100%)}
.btn svg{width:14px;height:14px}
.dots{left:571px;top:582px;display:flex;gap:6px}
.dots span{width:9px;height:9px;border-radius:50%;background:#fff}
.dots span.on{background:transparent;border:2px solid #fff}

.service-circle{width:178px;height:178px;border-radius:50%;border:5px solid var(--gold);display:flex;align-items:center;justify-content:center;text-align:center;font-size:13px;font-weight:700;line-height:1.5;text-shadow:0 1px 3px #000;z-index:2}

.section-title{font-family:"Poppins",sans-serif;font-size:44px;font-weight:500}
.section-title em{font-style:normal;color:var(--gold)}
.divider{width:120px;height:3px;background:var(--gold)}
.divider::after{content:"";position:absolute;left:50%;top:-5px;width:12px;height:12px;background:var(--gold);transform:translateX(-50%) rotate(45deg)}

.photo{display:block}
.text-panel h3{font-family:"Poppins",sans-serif;font-size:42px;font-weight:500;margin-bottom:18px}
.text-panel p{font-size:14px;line-height:30px;color:var(--muted);text-align:justify}
.faint-name{font-size:16px;letter-spacing:2px;color:rgba(255,255,255,.15);font-weight:700}

.tabs{left:111px;top:2052px;width:978px;height:50px;background:#222}
.tab{top:2069px;font-size:12px;font-weight:700}
.tab-active{left:111px;top:2052px;width:163px;height:50px}
.tile{width:238px;height:189px}
.tile-overlay{left:358px;top:2371px;width:239px;height:189px;background:rgba(20,20,30,.78);text-align:center;font-size:12px;font-weight:700;line-height:26px;padding-top:28px}
.arrow-box{width:45px;height:34px;background:#222;display:flex;align-items:center;justify-content:center}

.drilling{left:0;top:2795px;width:1200px;height:464px;background:radial-gradient(ellipse at 60% 40%,#2a2426,#141414 75%)}
.drilling-text{font-size:14px;line-height:33px;color:#ddd}

.avatar{border-radius:50%;background:linear-gradient(160deg,#8a7a6e,#3d3a3c);border:3px solid #3a3a3a}
.quote-text{font-size:14px;line-height:36px;color:#ddd}

.footer{left:0;top:4140px;width:1200px;height:252px;background:linear-gradient(180deg,#151515,#0f0f0f)}
.social{width:32px;height:32px;border:2px solid #fff;border-radius:50%}
.foot-link{top:4265px;font-size:14px;font-weight:700}
.copyright{top:4324px;font-size:12px}
</style>
</head>
<body>

<header>
  <div class="abs topbar">
    <div class="info" style="left:124px">
      <svg width="10" height="14" viewBox="0 0 10 14"><path d="M5 0a5 5 0 0 0-5 5c0 4 5 9 5 9s5-5 5-9a5 5 0 0 0-5-5zm0 7a2 2 0 1 1 0-4 2 2 0 0 1 0 4z" fill="#fff"/></svg>
      <span>140 , Lorem ipsum dolor , United States</span>
    </div>
    <div class="info" style="left:545px">
      <svg width="14" height="11" viewBox="0 0 14 11"><rect x="1" y="1" width="12" height="9" fill="none" stroke="#fff" stroke-width="1.4"/><path d="M1 1l6 5 6-5" fill="none" stroke="#fff" stroke-width="1.4"/></svg>
      <span>info@kvrglobalinks.example</span>
    </div>
    <div class="info phone" style="left:902px">
      <svg width="18" height="18" viewBox="0 0 24 24"><path d="M6.6 10.8a15 15 0 0 0 6.6 6.6l2.2-2.2a1 1 0 0 1 1-.25 11.4 11.4 0 0 0 3.6.57 1 1 0 0 1 1 1V20a1 1 0 0 1-1 1A17 17 0 0 1 3 4a1 1 0 0 1 1-1h3.5a1 1 0 0 1 1 1c0 1.25.2 2.45.57 3.57a1 1 0 0 1-.25 1z" fill="#fff"/></svg>
      <span>800 555 0142</span>
    </div>
  </div>
  <nav class="abs navbar" aria-label="Main"></nav>
  <div class="abs brand">KVR<br>GLOBALINKS</div>
  <a class="abs center nav-link active" style="left:387px">HOME</a>
  <a class="abs center nav-link" style="left:493px">ABOUT US</a>
  <a class="abs center nav-link" style="left:612px">PROJECTS</a>
  <a class="abs center nav-link" style="left:726px">CAREERS</a>
  <a class="abs center nav-link" style="left:864px">SUSTAINABILITY</a>
  <a class="abs center nav-link" style="left:1021px">NEWS &amp; MEDIA</a>
</header>

<section>
  <div class="abs hero" role="img" aria-label="Truck in front of a container port with an aircraft overhead at sunset"></div>
  <h1 class="abs hero-title">KVR GLOBALINKS</h1>
  <p class="abs hero-sub">Lorem ipsum dolor sit amet, consectetur adipiscing elit, sed do eiusmod tempor</p>
  <a class="abs btn" style="left:539px;top:436px;width:197px;height:53px">GET STARTED
    <svg viewBox="0 0 14 14"><circle cx="7" cy="7" r="7" fill="#fff"/><path d="M5.5 4l3 3-3 3" stroke="#c49a4f" stroke-width="1.8" fill="none"/></svg></a>
  <div class="abs dots"><span></span><span></span><span class="on"></span><span></span><span></span></div>

  <div class="abs service-circle" style="left:114px;top:649px;background:linear-gradient(150deg,#4a6a8c,#7a5a3c)" role="img" aria-label="Engineers in hard hats">INFRASTRUCTURE<br>CONSTRUCTION</div>
  <div class="abs service-circle" style="left:313px;top:649px;background:linear-gradient(150deg,#3a5f8f,#5a4a3a)" role="img" aria-label="Oil industry equipment">OIL</div>
  <div class="abs service-circle" style="left:511px;top:649px;background:linear-gradient(150deg,#2f4f7f,#8a6a2a)" role="img" aria-label="Energy and gas technician">ENEGY AND GAS<br>SERVICES</div>
  <div class="abs service-circle" style="left:711px;top:649px;background:linear-gradient(150deg,#6a7a6a,#3a4a3a)" role="img" aria-label="Farm workers in a field">AGRICULTURAL<br>PROJECTS</div>
  <div class="abs service-circle" style="left:910px;top:649px;background:linear-gradient(150deg,#8a4a3a,#c47a3a)" role="img" aria-label="Travellers on holiday">TRAVEL AND<br>TOURISM</div>
</section>

<section>
  <h2 class="abs center section-title" style="left:600px;top:920px">Our <em>Services</em></h2>
  <div class="abs divider" style="left:540px;top:998px"></div>

  <div class="abs photo" style="left:111px;top:1072px;width:489px;height:362px;background:linear-gradient(135deg,#3a5070,#6b4e3a 55%,#2c4468)" role="img" aria-label="Engineer with a clipboard at a container yard"></div>
  <div class="abs text-panel" style="left:600px;top:1072px;width:489px;height:362px;background:var(--panel);padding:42px 37px 0 37px">
    <h3>Trading</h3>
    <p>Sed ut perspiciatis unde omnis iste natus error sit voluptatem accusantium doloremque laudantium, totam rem aperiam, eaque ipsa quae ab illo inventore veritatis et quasi architecto beatae vitae dicta sunt explicabo.</p>
  </div>
  <a class="abs btn" style="left:648px;top:1328px;width:196px;height:51px">READ MORE
    <svg viewBox="0 0 14 14"><circle cx="7" cy="7" r="7" fill="#fff"/><path d="M5.5 4l3 3-3 3" stroke="#c49a4f" stroke-width="1.8" fill="none"/></svg></a>
  <div class="abs faint-name" style="left:925px;top:1356px">KVR GLOBALINKS</div>

  <div class="abs text-panel" style="left:111px;top:1434px;width:489px;height:364px;background:var(--panel-2);padding:42px 37px 0 37px">
    <h3>Contracting</h3>
    <p>Sed ut perspiciatis unde omnis iste natus error sit voluptatem accusantium doloremque laudantium, totam rem aperiam, eaque ipsa quae ab illo inventore veritatis et quasi architecto beatae vitae dicta sunt explicabo.</p>
  </div>
  <a class="abs btn" style="left:157px;top:1691px;width:198px;height:51px">READ MORE
    <svg viewBox="0 0 14 14"><circle cx="7" cy="7" r="7" fill="#fff"/><path d="M5.5 4l3 3-3 3" stroke="#c49a4f" stroke-width="1.8" fill="none"/></svg></a>
  <div class="abs faint-name" style="left:437px;top:1720px">KVR GLOBALINKS</div>
  <div class="abs photo" style="left:600px;top:1434px;width:489px;height:364px;background:linear-gradient(135deg,#5a5e78,#9a8f98 50%,#3e4560)" role="img" aria-label="Hands signing a contract document"></div>
</section>

<section>
  <h2 class="abs center section-title" style="left:600px;top:1902px">Our <em>Projects</em></h2>
  <div class="abs divider" style="left:540px;top:1980px"></div>

  <div class="abs tabs"></div>
  <div class="abs btn tab-active" style="font-size:12px">ALL PROJECTS</div>
  <span class="abs center tab" style="left:355px">CONSTRUCTION</span>
  <span class="abs center tab" style="left:518px">INDUSTRIAL</span>
  <span class="abs center tab" style="left:680px">TRADING</span>
  <span class="abs center tab" style="left:842px">TRAVEL &amp; TOURISM</span>
  <span class="abs center tab" style="left:1006px">AGRICULTURE</span>

  <div class="abs tile" style="left:111px;top:2173px;background:linear-gradient(135deg,#8a7a60,#4e6a4a)" role="img" aria-label="Workers inspecting produce in a factory"></div>
  <div class="abs tile" style="left:358px;top:2173px;background:linear-gradient(180deg,#7a94b8,#8a4a3a 70%,#3a5a8a)" role="img" aria-label="Cargo plane over stacked containers"></div>
  <div class="abs tile" style="left:605px;top:2173px;background:linear-gradient(135deg,#d8d8d8,#7a7a7a)" role="img" aria-label="Chefs preparing food in a kitchen"></div>
  <div class="abs tile" style="left:851px;top:2173px;background:linear-gradient(135deg,#c8c0b8,#5a5a6a)" role="img" aria-label="Travellers planning a trip with a world map"></div>
  <div class="abs tile" style="left:111px;top:2371px;background:linear-gradient(135deg,#8a8a7a,#3a4a3a)" role="img" aria-label="Technicians working on electrical equipment"></div>
  <div class="abs tile" style="left:358px;top:2371px;background:linear-gradient(135deg,#4a4a60,#222233)" role="img" aria-label="Project photo"></div>
  <div class="abs tile-overlay">SED UT PERSPICIATIS UNDE<br>OMNIS ISTE NATUS VOLUPTATEM<br>ACCUSANTIUM DOLORE</div>
  <a class="abs btn" style="left:403px;top:2487px;width:148px;height:38px;font-size:12px">VIEW PROJECTS</a>
  <div class="abs tile" style="left:605px;top:2371px;background:linear-gradient(135deg,#d0ccc8,#5a5e6a)" role="img" aria-label="Business partners shaking hands"></div>
  <div class="abs tile" style="left:851px;top:2371px;background:linear-gradient(135deg,#e8e4e0,#a89a8a)" role="img" aria-label="Hand signing papers beside a model house"></div>

  <div class="abs arrow-box" style="left:552px;top:2630px"><svg width="12" height="14" viewBox="0 0 12 14"><path d="M8 2L3 7l5 5" stroke="#fff" stroke-width="2" fill="none"/></svg></div>
  <div class="abs arrow-box" style="left:603px;top:2630px"><svg width="12" height="14" viewBox="0 0 12 14"><path d="M4 2l5 5-5 5" stroke="#fff" stroke-width="2" fill="none"/></svg></div>
</section>

<section>
  <div class="abs drilling" role="img" aria-label="Dim city skyline at night with a handshake"></div>
  <h2 class="abs center section-title" style="left:600px;top:2856px">Drilling &amp; <em>Gold Mines</em></h2>
  <div class="abs divider" style="left:540px;top:2933px"></div>
  <p class="abs center drilling-text" style="left:600px;top:2974px">Et harum quidem rerum facilis est et expedita distinctio. Nam libero tempore, cum soluta nobis<br>est eligendi optio cumque nihil impedit quo minus id quod maxime placeat facere possimus, omnis voluptas<br>assumenda est, omnis dolor repellendus. Temporibus autem quibusdam et aut officiis debitis<br>aut rerum necessitatibus saepe eveniet ut et voluptates repudiandae sint et molestiae.</p>
  <a class="abs btn" style="left:501px;top:3129px;width:198px;height:52px">READ MORE
    <svg viewBox="0 0 14 14"><circle cx="7" cy="7" r="7" fill="#fff"/><path d="M5.5 4l3 3-3 3" stroke="#c49a4f" stroke-width="1.8" fill="none"/></svg></a>
</section>

<section>
  <h2 class="abs center section-title" style="left:600px;top:3366px">What Our <em>Client Says</em></h2>
  <div class="abs divider" style="left:540px;top:3446px"></div>
  <div class="abs" style="left:250px;top:3578px;width:700px;height:480px;border-radius:50%;background:radial-gradient(ellipse,#262626,#1a1a1a 70%,transparent)" role="img" aria-label="Faint world map"></div>

  <div class="abs avatar" style="left:551px;top:3532px;width:68px;height:68px" role="img" aria-label="Client portrait"></div>
  <div class="abs avatar" style="left:312px;top:3583px;width:68px;height:68px" role="img" aria-label="Client portrait"></div>
  <div class="abs avatar" style="left:801px;top:3591px;width:68px;height:68px" role="img" aria-label="Client portrait"></div>
  <div class="abs avatar" style="left:201px;top:3730px;width:68px;height:68px" role="img" aria-label="Client portrait"></div>
  <div class="abs avatar" style="left:927px;top:3730px;width:68px;height:68px" role="img" aria-label="Client portrait"></div>
  <div class="abs avatar" style="left:312px;top:3915px;width:68px;height:68px" role="img" aria-label="Client portrait"></div>
  <div class="abs avatar" style="left:801px;top:3927px;width:68px;height:68px" role="img" aria-label="Client portrait"></div>
  <div class="abs avatar" style="left:551px;top:3978px;width:68px;height:68px" role="img" aria-label="Client portrait"></div>
  <div class="abs avatar" style="left:562px;top:3656px;width:76px;height:76px;border-color:#555" role="img" aria-label="Featured client portrait"></div>
  <div class="abs center" style="left:600px;top:3712px;font-family:'Poppins',sans-serif;font-size:44px;color:var(--gold);line-height:1">&rdquo;</div>

  <p class="abs center quote-text" style="left:600px;top:3766px">At vero eos et accusamus et iusto odio dignissimos ducimus<br>qui blanditiis praesentium voluptatum deleniti atque corrupti quosdolores<br>et quas molestias excepturi sint occaecati cupiditate.</p>
  <p class="abs center" style="left:600px;top:3889px;font-size:14px"><b>DANIEL MORROW</b> , Businessman</p>
</section>

<footer>
  <div class="abs footer"></div>
  <span class="abs social" style="left:519px;top:4186px" aria-label="Social profile"></span>
  <span class="abs social" style="left:564px;top:4186px" aria-label="Social profile"></span>
  <span class="abs social" style="left:604px;top:4186px" aria-label="Social profile"></span>
  <span class="abs social" style="left:647px;top:4186px" aria-label="Social profile"></span>
  <a class="abs center foot-link" style="left:266px">HOME</a>
  <a class="abs center foot-link" style="left:372px">ABOUT US</a>
  <a class="abs center foot-link" style="left:491px">PROJECTS</a>
  <a class="abs center foot-link" style="left:607px">CAREERS</a>
  <a class="abs center foot-link" style="left:741px">SUSTAINABILITY</a>
  <a class="abs center foot-link" style="left:900px">NEWS &amp; MEDIA</a>
  <p class="abs center copyright" style="left:600px">&copy; 2020 KVR GLOBALINKS. All Rights reserved</p>
</footer>

</body>
</html>
```